Business Card Design for Marketing Firm

Looking for business card design for higher end marketing firm. Clean but impressionable/trendy. We are a marketing firm that represents manufacturers in the foodservice equipment and supply industry. Our customers are end users such has hotels, restaurants, country clubs, convention centers and casinos as well as distributors of restaurants supplies and equipment, and manufacturers of foodservice equipment and supplies.
Target Market(s)
Hotels, Restaurants, Supply & Equipment Distributors, Foodservice Manufacturers
Industry/Entity Type
Foodservice/Hospitality
Contact Information for Business Card
Name, Title, Contact Number, Email, Website, Social Media, Address
Requirements
Must have
- Clean & Simple but Serious and Impressionable

```html
<!DOCTYPE html>
<html lang="en">
<head>
<meta charset="UTF-8">
<title>Harbor Hospitality Reps – Business Card</title>
<link href="https://fonts.googleapis.com/css2?family=Montserrat:wght@400;600&display=swap" rel="stylesheet">
<style>
  :root {
    --page-bg: #e9e7e3;
    --card-front: #ffffff;
    --card-back: #a3a3a3;
    --navy: #2b2d6b;
    --text: #4a4a4a;
    --back-mark: #d4d4d4;
  }
  * { box-sizing: border-box; margin: 0; padding: 0; }
  html, body { width: 900px; height: 1200px; overflow: hidden; }
  body {
    background: var(--page-bg);
    font-family: "Montserrat", sans-serif;
    position: relative;
  }
  .card {
    position: absolute;
    left: 90px;
    width: 720px;
    height: 410px;
    border-radius: 28px;
    box-shadow: 0 6px 18px rgba(0,0,0,0.18);
  }
  .card-front { top: 150px; background: var(--card-front); }
  .card-back  { top: 640px; background: var(--card-back); }

  .brand {
    position: absolute;
    font-family: "Montserrat", sans-serif;
    font-weight: 600;
    text-align: center;
    line-height: 1.2;
  }
  .card-front .brand {
    left: 40px; width: 330px; top: 140px;
    color: var(--navy);
    font-size: 25px;
  }
  .brand-dot {
    display: block;
    width: 44px; height: 44px;
    margin: 0 auto 16px;
    border-radius: 50%;
    background: currentColor;
  }
  .brand-line { display: block; }

  .divider {
    position: absolute;
    left: 392px; top: 120px;
    width: 3px; height: 175px;
    background: var(--navy);
  }
  .contact { position: absolute; left: 418px; top: 122px; color: var(--text); }
  .contact-name { font-weight: 600; font-size: 24px; color: var(--navy); }
  .contact-title { font-size: 14px; margin-top: 4px; }
  .contact-address { font-size: 14px; line-height: 1.45; margin-top: 22px; }
  .contact-list { list-style: none; margin-top: 18px; font-size: 14px; }
  .contact-list li { display: flex; align-items: center; gap: 9px; line-height: 1.65; }
  .contact-list svg { width: 13px; height: 13px; fill: var(--navy); flex: none; }

  .card-back .brand {
    left: 0; width: 100%; top: 110px;
    color: var(--back-mark);
    font-size: 40px;
  }
  .card-back .brand-dot { width: 60px; height: 60px; margin-bottom: 22px; }
</style>
</head>
<body>
  <section class="card card-front">
    <div class="brand"><span class="brand-dot"></span><span class="brand-line">Harbor Hospitality</span><span class="brand-line">Reps</span></div>
    <div class="divider"></div>
    <div class="contact">
      <p class="contact-name">Daniel Reyes</p>
      <p class="contact-title">CEO &amp; Founder</p>
      <p class="contact-address">420 Marlow Avenue, Suite 300<br>Bayview, CA 90000</p>
      <ul class="contact-list">
        <li><svg viewBox="0 0 24 24"><path d="M6.6 10.8a15.1 15.1 0 006.6 6.6l2.2-2.2a1 1 0 011-.25 11.4 11.4 0 003.6.57 1 1 0 011 1V20a1 1 0 01-1 1A17 17 0 013 4a1 1 0 011-1h3.5a1 1 0 011 1 11.4 11.4 0 00.57 3.6 1 1 0 01-.25 1z"/></svg>(555) 014-2288</li>
        <li><svg viewBox="0 0 24 24"><path d="M2 5h20v14H2z M2 5l10 8 10-8" fill="none" stroke="#2b2d6b" stroke-width="2.4"/></svg>info@harborhospitalityreps.com</li>
        <li><svg viewBox="0 0 24 24"><circle cx="12" cy="12" r="9.5" fill="none" stroke="#2b2d6b" stroke-width="2.4"/><path d="M2.5 12h19M12 2.5c3 3 3 16 0 19M12 2.5c-3 3-3 16 0 19" fill="none" stroke="#2b2d6b" stroke-width="2"/></svg>www.harborhospitalityreps.com</li>
      </ul>
    </div>
  </section>

  <section class="card card-back">
    <div class="brand"><span class="brand-dot"></span><span class="brand-line">Harbor Hospitality</span><span class="brand-line">Reps</span></div>
  </section>
</body>
</html>
```